Brand new letterhead, business card, email signature etc.

We are a financial company in London, UK. Our website is www.marlowvane.com. We're wanting a complete remodel of the company colours, letter head, business cards, email signatures, etc. Looking to keep the same font for the company name. I have upload a colour palette that we want to work with. We're looking for company letterhead for outgoing letters/ correspondence, letterhead for internal documentation, email signatures, e-letters. etc. Ultimately we will redesign the entire website also. It is important that our clients get a strong, secure, warm, trustworthy, solid feeling and first impression.
Updates

Designs look the same

Target Market(s)

Institutional investors, (ultra) high net worth individuals

Industry/Entity Type

Finance, Invesments banking.

Font styles to use
Other font styles liked:
• Current font is "Champagne & Limousines"

Requirements
Must have
• Must use the colours provided on the PDF uploaded to the portal. The purple = main colour. The red = accent colour.
Nice to have
• Nice to use same font as now for the company name "Corvane". Font is "Champagne & Limousines". Nice to have some reference to the old logo flower, but only subtle.
Should not have
• Do not use the colour red from our website. Use the colours provided on the colour palette PDF that I uploaded in the portal.

```html
<!DOCTYPE html>
<html lang="en">
<head>
<meta charset="utf-8">
<title>Corvane — Business Card</title>
<link href="https://fonts.googleapis.com/css2?family=Josefin+Sans:wght@300&family=Roboto:wght@400;700&display=swap" rel="stylesheet">
<style>
  :root {
    --backdrop: #3b3431;
    --card-white: #f7f7f7;
    --plum: #2a0019;
    --accent-red: #d4262b;
    --ink: #1a1a1a;
    --ink-name: #2a0019;
    --illustration-light: #ececec;
    --illustration-mid: #d8d8d8;
    --on-plum: #f4eef2;
  }
  * { box-sizing: border-box; margin: 0; padding: 0; }
  html, body { width: 1200px; height: 716px; overflow: hidden; }
  body {
    background: var(--backdrop);
    font-family: "Roboto", Arial, sans-serif;
    position: relative;
  }
  .card {
    position: absolute;
    top: 203px;
    width: 540px;
    height: 310px;
    box-shadow: 0 10px 24px rgba(0,0,0,0.45);
    overflow: hidden;
  }
  .card--front { left: 40px; background: var(--card-white); }
  .card--back { left: 620px; background: var(--plum); }

  .front__illustration {
    position: absolute;
    left: 0; top: 0;
    width: 270px; height: 310px;
    background: radial-gradient(circle at 45% 55%, var(--illustration-mid), var(--illustration-light) 70%, var(--card-white));
  }
  .front__wordmark {
    position: absolute;
    right: 36px; top: 48px;
    font-family: "Josefin Sans", "Century Gothic", sans-serif;
    font-weight: 300;
    font-size: 27px;
    letter-spacing: 6px;
    color: var(--ink);
  }
  .front__details {
    position: absolute;
    left: 300px; top: 112px;
  }
  .person__name {
    font-weight: 700;
    font-size: 18px;
    color: var(--ink-name);
  }
  .person__title {
    font-size: 13px;
    color: var(--accent-red);
    margin-top: 2px;
  }
  .address {
    font-size: 12.5px;
    line-height: 1.35;
    color: var(--ink);
    margin-top: 16px;
  }
  .contact-list {
    list-style: none;
    margin-top: 16px;
    font-size: 12.5px;
    line-height: 1.45;
    color: var(--ink);
  }
  .contact-list li { display: flex; align-items: center; gap: 7px; }
  .contact-list svg { width: 11px; height: 11px; fill: var(--accent-red); flex: none; }

  .back__lockup {
    position: absolute;
    left: 0; right: 0; top: 0; bottom: 0;
    display: flex;
    align-items: center;
    justify-content: center;
    gap: 22px;
  }
  .back__square {
    width: 66px; height: 66px;
    border: 1px solid var(--on-plum);
  }
  .back__wordmark {
    font-family: "Josefin Sans", "Century Gothic", sans-serif;
    font-weight: 300;
    font-size: 44px;
    letter-spacing: 10px;
    color: var(--on-plum);
  }
</style>
</head>
<body>
  <section class="card card--front">
    <div class="front__illustration" role="img" aria-label="Line illustration of a large flower with red-tipped stamens"></div>
    <div class="front__wordmark">CORVANE</div>
    <div class="front__details">
      <p class="person__name">Julian Ashcombe</p>
      <p class="person__title">President</p>
      <p class="address">27 Kestrel Row<br>London EC2V 7HN</p>
      <ul class="contact-list">
        <li>
          <svg viewBox="0 0 24 24" aria-hidden="true"><path d="M6.6 10.8a15 15 0 0 0 6.6 6.6l2.2-2.2a1 1 0 0 1 1-.25 11.4 11.4 0 0 0 3.6.57 1 1 0 0 1 1 1V20a1 1 0 0 1-1 1A17 17 0 0 1 3 4a1 1 0 0 1 1-1h3.5a1 1 0 0 1 1 1c0 1.25.2 2.45.57 3.57a1 1 0 0 1-.25 1z"/></svg>
          (020) 7946-0318
        </li>
        <li>
          <svg viewBox="0 0 24 24" aria-hidden="true"><path d="M2 5h20v14H2z M3 6l9 7 9-7" /></svg>
          name@marlowvane.com
        </li>
        <li>
          <svg viewBox="0 0 24 24" aria-hidden="true"><circle cx="12" cy="12" r="10"/></svg>
          www.marlowvane.com
        </li>
      </ul>
    </div>
  </section>

  <section class="card card--back">
    <div class="back__lockup">
      <div class="back__square" aria-hidden="true"></div>
      <div class="back__wordmark">CORVANE</div>
    </div>
  </section>
</body>
</html>
```